Heron Loan Partners Business Card

We need a business card design for our mortgage servicing company. In addition to servicing the loans of homeowners, we help homeowners with purchasing their homes and any mortgage refinancing. We would like to see designs that use the colors in the logo attached below (gold-ish yellow and navy blue), and any other design you deem fit! The design should communicate a simpler life with smart mortgages provided by Heron.

```html
<!DOCTYPE html>
<html lang="en">
<head>
<meta charset="utf-8">
<title>Heron Loan Partners Business Card</title>
<link href="https://fonts.googleapis.com/css2?family=Open+Sans:wght@400;700&display=swap" rel="stylesheet">
<style>
  :root {
    --backdrop: #2a2a2b;
    --card: #19191a;
    --card-back: #151516;
    --emboss: #232324;
    --gold: #e2b13a;
    --navy: #2b2b6b;
    --ink-light: #f2f2f2;
  }
  html, body {
    margin: 0;
    padding: 0;
    width: 1200px;
    height: 689px;
    overflow: hidden;
    background: var(--backdrop);
    font-family: "Open Sans", Arial, sans-serif;
  }
  .stage {
    position: relative;
    width: 1200px;
    height: 689px;
  }
  .card {
    position: absolute;
    top: 196px;
    width: 520px;
    height: 297px;
    border-radius: 16px;
    overflow: hidden;
  }
  .card--back {
    left: 45px;
    background: var(--card-back);
  }
  .card--front {
    left: 635px;
    background: var(--card);
  }
  .back-wordmark {
    position: absolute;
    left: 0;
    right: 0;
    top: 118px;
    text-align: center;
    font-weight: 700;
    font-size: 44px;
    color: var(--emboss);
    letter-spacing: 0.5px;
  }
  .front-wordmark {
    position: absolute;
    left: 196px;
    top: 50px;
    font-weight: 700;
    font-size: 30px;
    line-height: 1;
    color: var(--gold);
  }
  .front-wordmark .mark-dot {
    display: inline-block;
    width: 12px;
    height: 12px;
    border-radius: 50%;
    background: var(--navy);
    margin-right: 10px;
    vertical-align: middle;
  }
  .person {
    position: absolute;
    left: 34px;
    top: 128px;
  }
  .person__name {
    margin: 0;
    font-weight: 700;
    font-size: 22px;
    letter-spacing: 0.5px;
    color: var(--gold);
    text-transform: uppercase;
  }
  .person__title {
    margin: 2px 0 0;
    font-size: 15px;
    color: var(--ink-light);
  }
  .divider {
    position: absolute;
    left: 34px;
    right: 24px;
    top: 196px;
    height: 2px;
    background: var(--gold);
  }
  .contacts {
    position: absolute;
    left: 34px;
    top: 210px;
    margin: 0;
    padding: 0;
    list-style: none;
  }
  .contacts li {
    display: flex;
    align-items: center;
    gap: 8px;
    font-size: 14px;
    line-height: 23px;
    color: var(--ink-light);
  }
  .contacts svg {
    width: 12px;
    height: 12px;
    fill: var(--gold);
  }
  .address {
    position: absolute;
    right: 28px;
    top: 212px;
    margin: 0;
    text-align: right;
    font-size: 14px;
    line-height: 21px;
    color: var(--ink-light);
    font-style: normal;
  }
</style>
</head>
<body>
<main class="stage">
  <section class="card card--back" aria-label="Card back">
    <div class="back-wordmark">Heron Loan Partners</div>
  </section>

  <section class="card card--front" aria-label="Card front">
    <div class="front-wordmark"><span class="mark-dot"></span>Heron Loan Partners</div>

    <div class="person">
      <h1 class="person__name">Dale Corrigan</h1>
      <p class="person__title">Managing Director</p>
    </div>

    <div class="divider"></div>

    <ul class="contacts">
      <li>
        <svg viewBox="0 0 24 24" aria-hidden="true"><path d="M6.6 10.8a15.1 15.1 0 0 0 6.6 6.6l2.2-2.2a1 1 0 0 1 1-.25 11.4 11.4 0 0 0 3.6.57 1 1 0 0 1 1 1V20a1 1 0 0 1-1 1A17 17 0 0 1 3 4a1 1 0 0 1 1-1h3.5a1 1 0 0 1 1 1c0 1.25.2 2.45.57 3.6a1 1 0 0 1-.25 1z"/></svg>
        123 456 789
      </li>
      <li>
        <svg viewBox="0 0 24 24" aria-hidden="true"><path d="M2 5h20v14H2z M2 5l10 8 10-8" /></svg>
        info@heronloans.com
      </li>
      <li>
        <svg viewBox="0 0 24 24" aria-hidden="true"><circle cx="12" cy="12" r="10"/></svg>
        www.heronloans.com
      </li>
    </ul>

    <address class="address">Your address, City<br>State, Zip 1234</address>
  </section>
</main>
</body>
</html>
```